Law Firm Profile

I need a Law firm Profile design. Something professional, corporate inspired, unique and sophisticated. Preferred colours are blue, grey and white. Completion timeline is 5 days. Details of law firm are in the uploaded document

```html
<!DOCTYPE html>
<html lang="en">
<head>
<meta charset="utf-8">
<title>KLR Advocates – Law Firm Profile</title>
<link rel="stylesheet" href="https://fonts.googleapis.com/css2?family=Montserrat:ital,wght@0,400;0,500;0,600;0,700;0,800;1,700;1,800&display=swap">
<style>
  :root{
    --canvas:#e6e7ea;
    --blue:#0f63b8;
    --blue-deep:#0a4b96;
    --navy:#1b2f78;
    --sky:#4fc3f7;
    --accent:#1d6fc4;
    --grey:#cfd3da;
    --ink:#3b3f47;
    --white:#ffffff;
    --photo-warm-a:#2a2230;
    --photo-warm-b:#8a5a34;
    --photo-warm-c:#c9a26a;
  }
  *{box-sizing:border-box;margin:0;padding:0}
  html,body{width:720px;height:1200px;overflow:hidden;background:var(--canvas)}
  body{position:relative;font-family:"Montserrat",sans-serif;color:var(--ink)}
  .page{position:absolute;width:350px;height:495px;overflow:hidden;box-shadow:0 2px 10px rgba(0,0,0,.18)}
  .page svg.bg{position:absolute;inset:0;width:100%;height:100%}
  .back-cover{left:10px;top:70px}
  .front-cover{left:360px;top:70px}
  .inner-left{left:10px;top:625px;background:var(--white)}
  .inner-right{left:360px;top:625px;background:var(--white)}

  /* cover title */
  .cover-title{position:absolute;left:48px;top:200px;width:290px;color:var(--white)}
  .firm-name{font-weight:800;font-size:31px;letter-spacing:-.5px;line-height:1;white-space:nowrap}
  .firm-sub{font-weight:500;font-size:16px;letter-spacing:4px;margin-top:10px;padding-left:18px;white-space:nowrap}

  /* contact */
  .contact{position:absolute;left:40px;top:165px;width:300px;color:var(--white);text-align:center}
  .contact h3{color:var(--sky);font-size:10px;font-weight:700;letter-spacing:.8px;margin-bottom:12px}
  .contact p{font-size:9.5px;font-weight:700;line-height:1.45;margin-bottom:9px}

  /* inner text */
  .txt{position:absolute;font-size:5.6px;line-height:1.42;color:var(--ink)}
  .txt b{color:var(--accent);font-weight:800}
  .txt p{margin-bottom:5px}
  .intro{position:absolute;left:10px;top:140px;width:115px;color:var(--white);font-size:7.2px;font-weight:700;font-style:italic;line-height:1.42}
  .col-a{left:145px;top:140px;width:195px}
  .col-b{left:16px;top:362px;width:172px}
  .col-c{left:198px;top:305px;width:143px}

  .section-title{position:absolute;color:var(--accent);font-weight:800;font-style:italic;font-size:13px;letter-spacing:.3px}
  .rule{position:absolute;height:1px;background:var(--accent)}
  .person-photo{position:absolute;border-radius:2px}
  .person-name{position:absolute;color:var(--accent);font-weight:800;font-style:italic;font-size:7.4px}
  .person-role{position:absolute;font-weight:700;font-size:5.4px;letter-spacing:.4px;color:var(--ink)}
  .bio{width:235px}
  .structure-intro{left:20px;top:268px;width:190px}
  .structure-list{position:absolute;left:22px;top:300px;list-style:none;font-size:6.6px;font-weight:700;font-style:italic;color:var(--accent);line-height:1.65}
  .values{position:absolute;left:170px;top:382px;width:170px;color:var(--white)}
  .values h4{font-size:8.5px;font-weight:800;margin-bottom:4px}
  .values p{font-size:5.4px;line-height:1.45}
</style>
</head>
<body>

<!-- Back cover -->
<section class="page back-cover">
  <svg class="bg" viewBox="0 0 350 495">
    <defs>
      <linearGradient id="blueField" x1="0" y1="0" x2="0" y2="1">
        <stop offset="0" stop-color="#1a78cc"/><stop offset="1" stop-color="#0b57a8"/>
      </linearGradient>
      <linearGradient id="columnsTone" x1="0" y1="0" x2="0" y2="1">
        <stop offset="0" stop-color="#7fb3e6" stop-opacity=".35"/><stop offset="1" stop-color="#2f7fd0" stop-opacity=".15"/>
      </linearGradient>
    </defs>
    <rect width="350" height="495" fill="url(#blueField)"/>
    <rect x="0" y="0" width="350" height="230" fill="#2b74c4" opacity=".35" role="img" aria-label="Faint photo of lawyers meeting"/>
    <rect x="230" y="180" width="120" height="315" fill="url(#columnsTone)" role="img" aria-label="Faint photo of courthouse columns"/>
    <circle cx="190" cy="255" r="175" fill="#0b5cb0" opacity=".9"/>
  </svg>
  <div class="contact">
    <h3>CONTACT INFORMATION</h3>
    <p>Plot No. 14, Kafue Crescent, Riverside Park</p>
    <p>P.O. Box 40117, Lakeview, Lusaka, Zambia</p>
    <p>Cell: +260700111204, +260955300418,<br>+260977420631, +260761800295</p>
    <p>Tel: +260 211400782</p>
    <p>Email: info@klradvocates.example</p>
  </div>
</section>

<!-- Front cover -->
<section class="page front-cover">
  <svg class="bg" viewBox="0 0 350 495">
    <defs>
      <linearGradient id="coverBlue" x1="0" y1="0" x2="0" y2="1">
        <stop offset="0" stop-color="#1c79cf"/><stop offset="1" stop-color="#0b55a6"/>
      </linearGradient>
      <linearGradient id="scalesTone" x1="0" y1="0" x2="1" y2="1">
        <stop offset="0" stop-color="var(--photo-warm-a)"/><stop offset=".55" stop-color="var(--photo-warm-b)"/><stop offset="1" stop-color="var(--photo-warm-c)"/>
      </linearGradient>
      <linearGradient id="pillarsTone" x1="0" y1="0" x2="0" y2="1">
        <stop offset="0" stop-color="#8fc0ee" stop-opacity=".45"/><stop offset="1" stop-color="#2d7cd0" stop-opacity=".2"/>
      </linearGradient>
    </defs>
    <rect width="350" height="495" fill="url(#coverBlue)"/>
    <rect x="170" y="25" width="180" height="470" fill="url(#scalesTone)" role="img" aria-label="Photo of scales of justice on a desk and a courthouse facade"/>
    <rect x="60" y="300" width="230" height="195" fill="url(#pillarsTone)" role="img" aria-label="Photo of courthouse pillars"/>
    <path d="M30 250 A160 160 0 0 1 200 90 L200 120 A135 135 0 0 0 60 250 Z" fill="var(--grey)"/>
    <circle cx="185" cy="230" r="145" fill="var(--navy)" opacity=".93"/>
    <circle cx="230" cy="380" r="150" fill="#2d7fd4" opacity=".25"/>
  </svg>
  <div class="cover-title">
    <div class="firm-name">KLR ADVOCATES</div>
    <div class="firm-sub">Law Firm Profile</div>
  </div>
</section>

<!-- Inner spread: practice areas -->
<section class="page inner-left">
  <svg class="bg" viewBox="0 0 350 495">
    <defs>
      <clipPath id="lensClip"><ellipse cx="210" cy="35" rx="150" ry="75"/></clipPath>
    </defs>
    <path d="M0 118 C75 100 133 128 136 195 L136 300 C132 335 85 350 0 354 Z" fill="var(--blue)"/>
    <rect x="60" y="0" width="300" height="110" fill="#5a4a42" clip-path="url(#lensClip)" role="img" aria-label="Photo of lawyers reviewing documents in an office"/>
  </svg>
  <p class="intro">KLR Advocates is an established legal firm situated in Lusaka, Zambia. The firm was founded in 2013 by Mr Joseph M Lungu S.C., the current Director of Public Prosecutions. The firm represents a wide range of clients both local and international and is dedicated to providing the highest quality of services in various areas of the law including –</p>
  <div class="txt col-a">
    <p><b>CORPORATE LAW:</b> We provide comprehensive legal services for corporate clients in corporate governance, regulatory compliance, due diligence and risk management, ensuring every transaction is handled professionally and strategically.</p>
    <p><b>COMMERCIAL LAW:</b> We have vast knowledge and experience in complex commercial matters, including contract drafting, negotiation and compliance. Our lawyers keep pace with evolving rules of trade and the interplay between jurisdictions in a digital environment.</p>
    <p><b>ESTATE AND FAMILY LAW:</b> We are well versed in estate planning, wills, trusts, guardianship, divorce and probate, with a flexible approach that addresses each client's needs at every stage of the matter.</p>
  </div>
  <div class="txt col-b">
    <p><b>DEBT COLLECTION:</b> We efficiently handle the recovery process for businesses, financial institutions and individuals, ensuring that costs and disruptions are kept low.</p>
    <p><b>CIVIL AND CRIMINAL LITIGATION:</b> We have a notable track record in litigation and ancillary processes across commercial, criminal and constitutional courts, backed by meticulous analysis and sound strategy for the best results.</p>
    <p><b>ADMINISTRATIVE LAW:</b> We represent a significant number of clients in public law and have handled judicial review matters on immigration, licensing and regulatory infringements, offering clear guidance and swift response at every stage of the appeal process.</p>
  </div>
  <div class="txt col-c">
    <p>And;</p>
    <p><b>LAND LAW:</b> We have handled a wide range of land matters including trespass, encroachment, rectification and conveyancing, and manage a substantial caseload.</p>
    <p><b>CONSTITUTIONAL LAW:</b> We are a leading firm in constitutional matters and have handled presidential, parliamentary and local election petitions. Our strong database of case records and detailed understanding of constitutional law enable us to render well researched opinions to our clients.</p>
  </div>
</section>

<!-- Inner spread: personnel -->
<section class="page inner-right">
  <svg class="bg" viewBox="0 0 350 495">
    <defs>
      <radialGradient id="roundPhoto" cx=".5" cy=".45" r=".6">
        <stop offset="0" stop-color="#c9a26a"/><stop offset="1" stop-color="#1f2a3a"/>
      </radialGradient>
    </defs>
    <path d="M130 420 C140 360 200 340 260 345 C300 348 330 335 350 310 L350 495 L150 495 C135 470 128 445 130 420 Z" fill="var(--blue-deep)"/>
    <path d="M145 410 C155 365 205 352 262 356 C305 358 333 345 350 322" fill="none" stroke="var(--sky)" stroke-width="3" opacity=".6"/>
    <circle cx="280" cy="290" r="40" fill="url(#roundPhoto)" stroke="var(--white)" stroke-width="3" role="img" aria-label="Photo of scales of justice with legal icons"/>
  </svg>

  <h2 class="section-title" style="left:20px;top:16px">KEY PERSONNEL</h2>
  <div class="rule" style="left:130px;top:26px;width:200px"></div>

  <div class="person-photo" style="left:20px;top:48px;width:70px;height:62px;background:#8a6f9e" role="img" aria-label="Portrait of the managing partner"></div>
  <div class="person-name" style="left:100px;top:42px">NAOMI KASONDE</div>
  <div class="person-role" style="left:100px;top:52px">MANAGING PARTNER</div>
  <p class="txt bio" style="left:100px;top:61px">Naomi Kasonde has more than seven years of experience in commercial, mining, labour, construction, ICT and administrative law, as well as legislative drafting and civil litigation. She studied law at Central City University, graduated in 2015 and was admitted to the bar in 2016. She has sat on the licensing committee of the National Utilities Board and provides strategic legal advice to civil society groups. She holds a postgraduate diploma in legislative drafting.</p>

  <div class="person-photo" style="left:20px;top:150px;width:70px;height:68px;background:#6d5a50" role="img" aria-label="Portrait of the associate"></div>
  <div class="person-name" style="left:100px;top:146px">THANDIWE BANDA</div>
  <div class="person-role" style="left:100px;top:156px">ASSOCIATE</div>
  <p class="txt bio" style="left:100px;top:165px">Thandiwe Banda has over three years of experience in civil litigation, conveyancing, corporate and commercial transactions, contract drafting, family law, labour disputes and debt recovery. She studied at Northgate Open University, graduated in 2018 and was admitted to the bar in 2020. She is a member of the National Bar Association.</p>

  <h2 class="section-title" style="left:20px;top:244px">MANAGEMENT STRUCTURE</h2>
  <p class="txt structure-intro">We have a dedicated team of personnel whose primary goal is to provide the highest quality of service in compliance with all rules of professional conduct. Our support team works together to keep every client relationship well managed.</p>
  <ol class="structure-list">
    <li>1. MANAGING PARTNER</li>
    <li>2. PARTNER (S)</li>
    <li>3. ASSOCIATE (S)<br>&nbsp;&nbsp;&nbsp;&nbsp;SUPPORT STAFF:</li>
    <li>4. OFFICE MANAGER</li>
    <li>5. ASSISTANT OFFICE MANAGER</li>
    <li>6. LEGAL CLERK</li>
    <li>7. RECEPTIONIST</li>
  </ol>

  <div class="values">
    <h4>CORE VALUES</h4>
    <p>We take pride in the quality of our legal services, in which we uphold integrity, passion, credibility, continuous professional development and excellent client care. The firm is regulated by the National Bar Association, and adherence to legal ethics forms the backbone of our practice. We aim to harness creative, bespoke and expert solutions to meet every client's particular needs.</p>
  </div>
</section>

</body>
</html>
```